Transform Your Giving

I need a tri-fold brochure that will fit in a standard number 10 business envelope. Meadowlark and Allied Services is a charitable nonprofit. The goal of this brochure is to stimulate people into thinking about other ways to make a donation. The design should communicate the essential information on donation options, create a sense of professional integrity, be graphically sharp, easy to read and laid out in a way that doesn't make the material appear crowded.

```html
<!DOCTYPE html>
<html lang="en">
<head>
<meta charset="utf-8">
<title>Transform Your Giving – Tri-fold Brochure</title>
<link href="https://fonts.googleapis.com/css2?family=Poppins:ital,wght@0,400;0,500;0,600;0,700;0,800;1,500;1,600&display=swap" rel="stylesheet">
<style>
:root{
  --navy:#2b2574;
  --green:#43b649;
  --ink:#1f1f2b;
  --paper:#ffffff;
  --backdrop:#cfcfcf;
  --muted:#e9e9ee;
}
*{box-sizing:border-box;margin:0;padding:0}
html,body{width:800px;height:1200px;overflow:hidden}
body{background:var(--backdrop);font-family:'Poppins',sans-serif;color:var(--ink);position:relative}
.sheet{position:absolute;background:var(--paper);overflow:hidden;box-shadow:0 2px 6px rgba(0,0,0,.18)}
.sheet-outside{left:65px;top:67px;width:672px;height:519px}
.sheet-inside{left:66px;top:615px;width:670px;height:517px}
.panel{position:absolute;top:0;height:100%;width:224px}
.abs{position:absolute}
.navy{color:var(--navy)}
.green{color:var(--green)}
.heading{font-weight:700;font-size:11px;letter-spacing:.1px;line-height:1.1}
.body-text{font-size:6.9px;line-height:1.2;text-align:justify}
.lead-italic{font-style:italic;font-weight:600;font-size:6.7px;line-height:1.22}
.icon{position:absolute;border-radius:50%;background:#fff;display:flex;align-items:center;justify-content:center}
.icon-navy{border:2px solid var(--navy)}
.icon-green{border:2px solid var(--green)}
.icon svg{width:60%;height:60%}
.photo{position:absolute}
.brand{display:flex;align-items:center;gap:4px;font-weight:800;letter-spacing:1px}
.brand-dot{border-radius:50%;background:var(--green)}

/* outside: gift options list */
.options-box{left:32px;top:122px;width:165px;height:146px;border:1px solid var(--green);border-radius:5px}
.option{position:absolute;left:26px;display:flex;align-items:center;gap:7px;font-size:10.5px;font-weight:500}
.option .icon{position:static;width:23px;height:23px}

/* outside middle */
.mid-panel{left:224px;width:223px;background:var(--navy);color:#fff}
.mid-intro{left:24px;top:88px;width:176px;text-align:center;font-size:7.4px;font-weight:700;line-height:1.25}
.quote-box{left:26px;top:168px;width:172px;height:43px;border:1px solid var(--green);border-radius:5px;overflow:hidden}
.quote-box p{font-size:7px;font-style:italic;text-align:center;margin-top:6px;line-height:1.25}
.quote-author{position:absolute;left:0;bottom:0;width:100%;height:15px;background:var(--green);font-weight:700;font-size:8.5px;text-align:center;line-height:15px}
.will-pill{left:28px;top:236px;width:168px;height:16px;border:1px solid var(--green);border-radius:8px;text-align:center;font-weight:700;font-size:12.5px;color:var(--green);line-height:14px;letter-spacing:.6px}
.contact-card{left:17px;top:287px;width:190px;height:232px;background:var(--green);border-radius:8px 8px 0 0}
.contact-tab{left:34px;top:0;width:122px;height:23px;background:#fff;border-radius:0 0 12px 12px;color:var(--navy);font-weight:700;font-size:13.5px;text-align:center;line-height:23px}
.contact-line{position:absolute;left:0;width:100%;text-align:center;font-size:7px;color:var(--ink)}
.contact-icon{position:absolute;left:88px;width:12px;height:12px;border-radius:50%;background:var(--navy);display:flex;align-items:center;justify-content:center}
.contact-icon svg{width:7px;height:7px}
.disclaimer{left:12px;top:178px;width:166px;font-size:4.6px;text-align:center;line-height:1.3;color:var(--ink)}

/* outside right cover */
.cover{left:447px;width:225px}
.cover-title{width:100%;text-align:center;font-weight:800;line-height:1}

/* inside */
.intro-lines{left:20px;top:33px;width:181px;text-align:right;font-size:6.9px;line-height:8px;white-space:nowrap}
.section-title{font-weight:700;font-size:8.2px;line-height:1.15}
.how{font-weight:700;font-size:9.8px;color:var(--navy)}
.how span{color:var(--green)}
.check-list{list-style:none}
.check-list li{position:relative;padding-left:10px;margin-bottom:4px}
.check-list li::before{content:"";position:absolute;left:0;top:1.5px;width:5px;height:5px;border-radius:50%;background:var(--green)}
.dash-rule{position:absolute;border-top:1px dashed #9a9a9a;height:0}
</style>
</head>
<body>

<!-- ================= OUTSIDE SHEET ================= -->
<section class="sheet sheet-outside">

  <!-- inside flap: impact -->
  <div class="panel" style="left:0">
    <h2 class="heading navy abs" style="left:26px;top:27px;font-size:11.5px">THE IMPACT <span class="green">OF</span> YOUR <span class="green">GIFT</span></h2>
    <p class="body-text abs" style="left:26px;top:45px;width:172px;font-size:7.3px">Your generosity drives our mission. With every Smart gift you're supporting Meadowlark and Allied Services. Join our community of Smart Givers today and make an enduring impact. With Smart Giving your generosity reaches further. Begin your Smart Giving journey with us today.</p>

    <div class="options-box abs"></div>
    <div class="option" style="left:26px;top:130px"><span class="icon icon-navy"><svg viewBox="0 0 20 20"><circle cx="10" cy="10" r="7" fill="none" stroke="#2b2574" stroke-width="1.5"/><path d="M12.5 7.5a3.5 3.5 0 1 0 0 5" fill="none" stroke="#2b2574" stroke-width="1.5"/></svg></span>Crypto</div>
    <div class="option" style="left:26px;top:156px"><span class="icon icon-green"><svg viewBox="0 0 20 20"><path d="M3 7 10 3l7 4z M4 8h12 M5 9v6 M8 9v6 M12 9v6 M15 9v6 M3 16h14" fill="none" stroke="#2b2574" stroke-width="1.3"/></svg></span>DAF's</div>
    <div class="option" style="left:26px;top:183px"><span class="icon icon-navy"><svg viewBox="0 0 20 20"><path d="M4 16V12 M8 16V9 M12 16V11 M16 16V6 M3 17h14" fill="none" stroke="#2b2574" stroke-width="1.5"/></svg></span>Stocks &amp; Securities</div>
    <div class="option" style="left:26px;top:210px"><span class="icon icon-green"><svg viewBox="0 0 20 20"><rect x="4" y="8" width="12" height="9" fill="none" stroke="#2b2574" stroke-width="1.3"/><path d="M3 6h14v2H3z M10 6v11" fill="none" stroke="#2b2574" stroke-width="1.3"/></svg></span>QCDs</div>
    <div class="option" style="left:26px;top:236px"><span class="icon icon-navy"><svg viewBox="0 0 20 20"><circle cx="10" cy="7" r="3" fill="none" stroke="#2b2574" stroke-width="1.3"/><path d="M3 10c2 4 4 6 7 6s5-2 7-6" fill="none" stroke="#2b2574" stroke-width="1.3"/></svg></span>Charitable Annuity</div>

    <div class="photo" role="img" aria-label="Photo of a smiling couple packing a donations box together" style="left:0;top:285px;width:224px;height:234px;background:linear-gradient(160deg,#eef0f2 0%,#c7d6dc 35%,#8aa7b8 60%,#d3b493 85%,#c19e78 100%)"></div>
  </div>

  <!-- back panel: contact -->
  <div class="panel mid-panel">
    <div class="brand abs" style="left:0;width:223px;top:38px;justify-content:center;font-size:27px;color:#fff"><span class="brand-dot" style="width:9px;height:9px"></span>MAAS</div>
    <p class="mid-intro abs"><span class="green">To learn more about Smart Giving Options and how they can benefit you and</span> Meadowlark and Allied Services, please reach out to our team. We're here to help you navigate these giving methods and answer any question you may have.</p>

    <svg class="abs" style="left:103px;top:159px" width="18" height="11" viewBox="0 0 18 11"><path d="M1 11V6C1 3 3 1 7 0v2C5 3 4 4 4 5h3v6z M10 11V6c0-3 2-5 6-6v2c-2 1-3 2-3 3h3v6z" fill="#43b649"/></svg>
    <div class="quote-box abs">
      <p>Being kind to others is a way of being<br>good to yourself.</p>
      <div class="quote-author">MIRIAM KESSLER</div>
    </div>

    <p class="abs" style="left:0;top:222px;width:223px;text-align:center;font-size:8.2px">If you do not have a will, go to</p>
    <div class="will-pill abs">www.WillReady.org</div>
    <p class="abs" style="left:0;top:255px;width:223px;text-align:center;font-size:8.2px;line-height:1.2">In 20 minutes you can have a legal<br>will – for free</p>

    <div class="contact-card abs">
      <div class="contact-tab abs">CONTACT US</div>
      <h3 class="abs" style="left:0;top:28px;width:190px;text-align:center;font-size:11.5px;font-weight:700;color:var(--ink)">HAVE MORE QUESTION?</h3>
      <p class="contact-line" style="top:42px;line-height:1.25">Please contact us at Meadowlark and<br>Allied Services</p>

      <span class="contact-icon" style="top:64px"><svg viewBox="0 0 10 10"><path d="M2 1l2 2-1 1c1 1.5 2 2.5 3 3l1-1 2 2-1.5 1.5C4 9 1 6 .5 2.5z" fill="#fff"/></svg></span>
      <p class="contact-line" style="top:79px">555-014-2200 (ext. 100)</p>
      <span class="contact-icon" style="top:88px"><svg viewBox="0 0 10 10"><rect x="1" y="2.5" width="8" height="5.5" fill="#fff"/><path d="M1 2.5l4 3 4-3" fill="none" stroke="#2b2574" stroke-width=".9"/></svg></span>
      <p class="contact-line" style="top:102px">jmarlow@meadowlarkas.org</p>
      <span class="contact-icon" style="top:113px"><svg viewBox="0 0 10 10"><path d="M5 9.5C3 7 2 5.5 2 4a3 3 0 0 1 6 0c0 1.5-1 3-3 5.5z" fill="#fff"/><circle cx="5" cy="4" r="1.1" fill="#2b2574"/></svg></span>
      <p class="contact-line" style="top:128px">1420 Prairie View Rd. Suite 2 Fargo, ND 58102</p>
      <span class="contact-icon" style="top:137px"><svg viewBox="0 0 10 10"><circle cx="5" cy="5" r="4" fill="none" stroke="#fff" stroke-width=".9"/><path d="M1 5h8 M5 1c-2 2.5-2 5.5 0 8 M5 1c2 2.5 2 5.5 0 8" fill="none" stroke="#fff" stroke-width=".7"/></svg></span>
      <p class="contact-line" style="top:151px">www.meadowlarkas.org</p>

      <p class="abs" style="left:21px;top:165px;font-size:8.5px;color:var(--ink)">Follow us</p>
      <div class="dash-rule" style="left:65px;top:172px;width:103px;border-color:#2b2574"></div>
      <p class="disclaimer abs">This material has been prepared for informational purposes only and is not intended to provide tax, accounting, or legal advice. Meadowlark and Allied Services is not a professional fiduciary organization. Please consult with your tax advisor or financial professional before making a decision about Smart Giving</p>
    </div>
  </div>

  <!-- front cover -->
  <div class="panel cover">
    <h1 class="cover-title abs navy" style="top:24px;font-size:19.5px">TRANSFORM</h1>
    <p class="cover-title abs green" style="top:45px;font-size:19.5px">YOUR GIVING</p>
    <div class="abs" style="left:27px;top:73px;width:171px;height:1px;background:#bdbdbd"></div>
    <div class="abs" style="left:89px;top:71px;width:47px;height:4px;border-radius:2px;background:var(--green)"></div>
    <p class="cover-title abs navy" style="top:87px;font-size:26px">BE STRATEGIC</p>
    <p class="cover-title abs navy" style="top:112px;font-size:26px">BE SMART</p>
    <p class="abs" style="left:0;top:143px;width:225px;text-align:center;font-size:11.2px;line-height:1.2">Discover the impact of Smart<br>Giving with Meadowlark<br>and Allied Services</p>

    <svg class="abs" style="left:0;top:195px" width="225" height="220" viewBox="0 0 225 220">
      <defs>
        <linearGradient id="coverBand" x1="0" y1="0" x2="0" y2="1">
          <stop offset="0" stop-color="#ffffff"/><stop offset=".35" stop-color="#cfd0d0"/><stop offset="1" stop-color="#8c8f8a"/>
        </linearGradient>
      </defs>
      <rect x="0" y="50" width="225" height="150" fill="url(#coverBand)"/>
      <path d="M0 190 L0 160 L30 175 Z" fill="#2b2574"/>
      <path d="M225 190 L225 160 L195 175 Z" fill="#2b2574"/>
      <polygon points="112,0 90,42 134,42" fill="#2b2574"/>
      <path d="M40 70 A85 85 0 0 1 185 70" fill="none" stroke="#43b649" stroke-width="1" stroke-dasharray="3 2"/>
      <path d="M20 150 A98 98 0 0 1 30 100 M205 150 A98 98 0 0 0 195 100" fill="none" stroke="#43b649" stroke-width="1" stroke-dasharray="3 2"/>
      <path d="M0 205 Q112 165 225 205 L225 220 L0 220 Z" fill="#fff"/>
      <path d="M0 203 Q112 160 225 203" fill="none" stroke="#43b649" stroke-width="4"/>
      <g fill="#fff" stroke="#2b2574" stroke-width="1.6">
        <circle cx="36" cy="76" r="9"/><circle cx="18" cy="115" r="9"/><circle cx="17" cy="158" r="9"/>
        <circle cx="191" cy="76" r="9"/><circle cx="208" cy="115" r="9" stroke="#43b649"/><circle cx="207" cy="158" r="9"/>
      </g>
    </svg>
    <div class="photo" role="img" aria-label="Photo of one hand passing banknotes to another hand" style="left:42px;top:263px;width:141px;height:125px;border-radius:70px 70px 20px 20px;background:radial-gradient(circle at 50% 45%,#f1e3d4 0%,#d8c2aa 40%,#b9b8b0 75%,#9a9c98 100%)"></div>

    <div class="brand abs navy" style="left:0;width:225px;top:425px;justify-content:center;font-size:25px"><span class="brand-dot" style="width:8px;height:8px"></span>MAAS</div>
    <p class="abs" style="left:0;top:475px;width:225px;text-align:center;font-size:12.5px;letter-spacing:1.2px;font-weight:500">www.<span class="green" style="font-weight:700">meadowlarkas</span>.org</p>
  </div>
</section>

<!-- ================= INSIDE SHEET ================= -->
<section class="sheet sheet-inside">

  <!-- inside left: intro + stocks -->
  <div class="panel" style="left:0">
    <svg class="abs" style="left:0;top:0" width="80" height="79" viewBox="0 0 80 79"><polygon points="0,0 80,0 0,79" fill="#2b2574"/></svg>
    <p class="intro-lines abs">We would like to introduce you to five<br>Strategic and Smart ways to give that could<br>potentially be more beneficial to you compared<br>to traditional cash donations.</p>
    <p class="abs" style="left:25px;top:75px;width:175px;font-size:6.9px;line-height:1.2">We encourage you to keep this information as<br>a guide for your future contributions.</p>

    <span class="icon icon-navy" style="left:25px;top:98px;width:30px;height:30px"><svg viewBox="0 0 20 20"><path d="M4 16V12 M8 16V9 M12 16V11 M16 16V6 M3 17h14" fill="none" stroke="#2b2574" stroke-width="1.4"/></svg></span>
    <h3 class="section-title abs navy" style="left:61px;top:98px;width:150px">GIFTS OF STOCKS OR APPRECIATED <span class="green">ASSETS STRATEGIC &amp; SMART</span></h3>
    <p class="lead-italic abs" style="left:61px;top:121px;width:145px">Consider your long-term publicly traded stock as a way to give to your favorite charity.</p>
    <p class="body-text abs" style="left:25px;top:150px;width:175px">You can make a significantly bigger impact when you donate long-term appreciated securities, including stock, mutual funds, and bonds, directly to your favorite charity.</p>
    <h4 class="how abs" style="left:25px;top:188px">HOW DOES <span>IT WORK?</span></h4>
    <p class="body-text abs" style="left:25px;top:205px;width:175px">When you donate stock to a charity, you will generally take a tax deduction for the full market value. Because you are donating stock, your contribution and tax deduction may be significantly higher than contributing the after-tax proceeds. The same benefits apply when you donate mutual funds or bonds.</p>

    <div class="photo" role="img" aria-label="Photo of two volunteers packing food into donation boxes" style="left:0;top:275px;width:224px;height:242px;background:linear-gradient(180deg,#ffffff 0%,#efe7de 25%,#d9c1a3 55%,#c9a57d 80%,#e8e4df 100%)"></div>
  </div>

  <!-- inside middle: DAF + QCD -->
  <div class="panel" style="left:224px">
    <span class="icon icon-green" style="left:19px;top:29px;width:30px;height:30px"><svg viewBox="0 0 20 20"><path d="M3 7 10 3l7 4z M4 8h12 M5 9v6 M8 9v6 M12 9v6 M15 9v6 M3 16h14" fill="none" stroke="#2b2574" stroke-width="1.3"/></svg></span>
    <h3 class="section-title abs navy" style="left:58px;top:30px;font-size:8.8px">DONOR-ADVISED FUND (DAF)<br><span class="green">STRATEGIC &amp; SMART</span></h3>
    <p class="lead-italic abs" style="left:58px;top:53px;width:140px">Consider a DAF – a simple, flexible, and tax-advantageous way to give to your favorite charities.</p>
    <p class="abs" style="left:20px;top:87px;width:170px;font-size:7.5px;line-height:1.2">A Donor-Advised Fund (DAF), is like a charitable investment account for the sole purpose of supporting your favorite charities.</p>
    <h4 class="how abs" style="left:20px;top:132px">HOW DOES <span>IT WORK?</span></h4>
    <p class="body-text abs" style="left:20px;top:149px;width:180px">You establish a DAF and contribute cash, stocks, or non-publicly traded assets, cryptocurrency, and private company stock to be eligible for an immediate tax deduction. Those funds are contributed for tax-free growth. You can recommend grants be made from your DAF to any IRS qualified public charity</p>
    <div class="dash-rule" style="left:20px;top:225px;width:172px"></div>

    <span class="icon icon-green" style="left:19px;top:242px;width:30px;height:30px"><svg viewBox="0 0 20 20"><rect x="4" y="8" width="12" height="9" fill="none" stroke="#2b2574" stroke-width="1.3"/><path d="M3 6h14v2H3z M10 6v11" fill="none" stroke="#2b2574" stroke-width="1.3"/></svg></span>
    <h3 class="section-title abs navy" style="left:56px;top:245px;width:150px;font-size:8.2px">QUALIFIED CHARITABLE <span class="green">DISTRIBUTIONS (QCDS) STRATEGIC &amp; SMART</span></h3>
    <p class="lead-italic abs" style="left:56px;top:277px;width:145px">Consider a QCD – when planning your IRA withdrawal strategy...and donate to your favorite charity.</p>
    <p class="body-text abs" style="left:17px;top:315px;width:185px">IRA owners at age 70 ½ or over can transfer dollars from their IRA to charity tax-free each year. These transfers known as Qualified Charitable Distributions (QCDs) offer eligible older Americans a great way to easily give to charity.</p>
    <h4 class="how abs" style="left:17px;top:359px">HOW DOES <span>IT WORK?</span></h4>
    <p class="body-text abs" style="left:17px;top:377px;width:185px"><b>Are you 72 and required to take a minimum distribution (RMD) from your IRA but do not need the funds?</b> Consider a Qualified Charitable Distribution. Normally, distributions from a traditional IRA are taxable when received. With a QCD, these distributions become tax-free when paid directly from the IRA to your favorite eligible charity. An IRA owner wishing to make a QCD should contact their IRA trustee, allowing time to complete the transaction before the end of the year to receive the tax benefit.</p>
    <p class="abs" style="left:0;top:480px;width:224px;text-align:center;font-size:10px;letter-spacing:1px;font-weight:500">www.<span class="green" style="font-weight:700">meadowlarkas</span>.org</p>
  </div>

  <!-- inside right: crypto + annuity -->
  <div class="panel" style="left:447px;width:223px">
    <span class="icon icon-navy" style="left:15px;top:28px;width:31px;height:31px"><svg viewBox="0 0 20 20"><circle cx="10" cy="10" r="7" fill="none" stroke="#2b2574" stroke-width="1.4"/><path d="M12.5 7.5a3.5 3.5 0 1 0 0 5" fill="none" stroke="#2b2574" stroke-width="1.4"/></svg></span>
    <h3 class="section-title abs navy" style="left:52px;top:28px;font-size:8.8px">CRYPTOCURRENCY<br><span class="green">STRATEGIC &amp; SMART</span></h3>
    <p class="lead-italic abs" style="left:52px;top:52px;width:150px">Consider donating Bitcoin and other cryptocurrencies to your favorite charity.</p>
    <p class="body-text abs" style="left:17px;top:74px;width:185px">Bitcoin and other cryptocurrencies can be donated to charity just like other appreciated assets such as stocks and other business interests. Before you sell bitcoin and donate the after-tax proceeds, consider donating your bitcoin directly to a favorite charity.</p>
    <h4 class="how abs" style="left:17px;top:119px">HOW DOES <span>IT WORK?</span></h4>
    <p class="body-text abs" style="left:17px;top:136px;width:185px">Many donors find it useful to open a Donor-Advised Fund (DAF). This strategy includes two significant benefits, both for you and your favorite charity.</p>
    <ul class="check-list body-text abs" style="left:19px;top:167px;width:183px;text-align:left">
      <li>Your tax deduction will be equal to the fair market value of the donated bitcoin (as determined by a qualified appraisal).</li>
      <li>Your cryptocurrency donation is tax-smart because it may eliminate capital gains on the value / appreciation AND your favorite charity will receive 100% of the value of the contribution.</li>
    </ul>
    <p class="body-text abs" style="left:18px;top:237px;width:183px;text-align:left">Often charities are not able to accept direct donations of bitcoin/crypto so using a DAF is a great way to donate these assets.</p>
    <div class="dash-rule" style="left:17px;top:267px;width:182px"></div>

    <span class="icon icon-navy" style="left:17px;top:283px;width:30px;height:30px"><svg viewBox="0 0 20 20"><circle cx="10" cy="7" r="3" fill="none" stroke="#2b2574" stroke-width="1.3"/><path d="M3 10c2 4 4 6 7 6s5-2 7-6" fill="none" stroke="#2b2574" stroke-width="1.3"/></svg></span>
    <h3 class="section-title abs navy" style="left:53px;top:283px;font-size:8.4px">CHARITABLE GIFT ANNUITY<br><span class="green">STRATEGIC &amp; SMART</span></h3>
    <p class="lead-italic abs" style="left:53px;top:305px;width:150px">Consider establishing a Charitable Gift Annuity</p>
    <p class="abs" style="left:18px;top:329px;width:185px;font-size:6.9px;line-height:1.2">You make a donation to a single charity. The gift is set aside in a reserve account and invested.</p>
    <h4 class="how abs" style="left:18px;top:351px">HOW DOES <span>IT WORK?</span></h4>
    <p class="body-text abs" style="left:18px;top:368px;width:185px">A charitable gift annuity is a contract between a donor and a charity. As a donor, you make a sizable gift to charity using cash, securities, or possibly other assets. This money is then invested. In return, you become eligible to take a partial tax deduction for your donation, plus you receive a fixed stream of income from the charity for the rest of your life. At the end of your life (as well as your spouse's, if you're giving as a couple), the charity receives the remainder of the gift.</p>

    <div class="brand abs navy" style="left:0;width:168px;top:455px;justify-content:center;font-size:19px"><span class="brand-dot" style="width:7px;height:7px"></span>MAAS</div>
    <svg class="abs" style="left:131px;top:425px" width="92" height="92" viewBox="0 0 92 92"><polygon points="92,0 92,92 0,92" fill="#43b649"/></svg>
  </div>
</section>

</body>
</html>
```